Electrician Letterhead Design MVR

We need some letterhead for our bills and other papers.
Customer address is on the right side (Swiss format)
A4 format

Design should also be applicable on Cards

Target Market(s)

Private Customers, Small Business

Industry/Entity Type

Electrician

Other font styles liked:
• incised 901

Colors
00AB8E
00BBA5
67D7C9
C6EFE9
E9F9F6

```html
<!DOCTYPE html>
<html lang="en">
<head>
<meta charset="utf-8">
<title>MVR Letterhead</title>
<link rel="stylesheet" href="https://fonts.googleapis.com/css2?family=Open+Sans:wght@400;600;700&family=Roboto:wght@400&display=swap">
<style>
  :root {
    --brand: #229f90;
    --backdrop: #dedede;
    --paper: #f8f8f8;
    --ink: #3a3a3a;
    --body-ink: #5d5d5d;
    --sign-tone: #d9dde3;
  }
  * { margin: 0; padding: 0; box-sizing: border-box; }
  html, body {
    width: 1153px; height: 1200px; overflow: hidden;
    background: var(--backdrop);
  }
  .letterhead {
    position: absolute; left: 160px; top: 20px;
    width: 833px; height: 1160px;
    background: var(--paper);
    box-shadow: 0 6px 24px rgba(0,0,0,0.12);
    overflow: hidden;
  }
  .brand-name {
    position: absolute; left: 82px; top: 64px;
    font-family: "Open Sans", sans-serif; font-weight: 700;
    font-size: 62px; line-height: 1; color: var(--brand);
    letter-spacing: 1px;
  }
  .brand-legal {
    position: absolute; left: 82px; top: 136px;
    font-family: "Open Sans", sans-serif; font-weight: 600;
    font-size: 11px; color: #111; letter-spacing: 0.3px;
  }
  .sender {
    position: absolute; left: 82px; top: 173px;
    font-family: "Roboto", sans-serif; font-size: 14.5px;
    line-height: 18px; color: var(--ink);
  }
  .contacts {
    position: absolute; left: 82px; top: 216px; list-style: none;
    font-family: "Roboto", sans-serif; font-size: 14.5px;
    line-height: 18.5px; color: var(--ink);
  }
  .contacts li { display: flex; align-items: center; gap: 7px; }
  .contacts svg { width: 14px; height: 14px; fill: var(--brand); flex: none; }
  .letter-body {
    position: absolute; left: 82px; top: 354px; width: 668px;
    font-family: "Open Sans", sans-serif; font-size: 14.9px;
    line-height: 22px; color: var(--body-ink);
  }
  .salutation { margin-bottom: 22px; }
  .letter-body p.para { text-align: justify; margin-bottom: 22px; }
  .closing { margin-top: 0; }
  .signature {
    position: absolute; left: 82px; top: 935px;
    width: 100px; height: 90px;
    background: linear-gradient(135deg, var(--paper), var(--sign-tone), var(--paper));
    border-radius: 6px;
  }
  .footer-band {
    position: absolute; left: 0; bottom: 0;
    width: 100%; height: 19px; background: var(--brand);
  }
</style>
</head>
<body>
  <main class="letterhead">
    <div class="brand-name">MVR</div>
    <div class="brand-legal">Elektrotechnik Vollmer GmbH</div>

    <address class="sender" style="font-style:normal">
      Lindenweg 14 04109<br>
      City Leipzig Germany
    </address>

    <ul class="contacts">
      <li>
        <svg viewBox="0 0 16 16" aria-hidden="true"><path d="M2 5c0-2 2-3 6-3s6 1 6 3v1h-3V5H5v1H2zM4 7h8l2 5v2H2v-2zm4 2a2 2 0 1 0 0 4 2 2 0 0 0 0-4z"/></svg>
        555.014.2290
      </li>
      <li>
        <svg viewBox="0 0 16 16" aria-hidden="true"><path d="M1 3h14v1L8 9 1 4zm0 3 7 5 7-5v7H1z"/></svg>
        info@mvr-elektro.com
      </li>
      <li>
        <svg viewBox="0 0 16 16" aria-hidden="true"><path d="M8 1a7 7 0 1 0 0 14A7 7 0 0 0 8 1zm-1 2c-1 1 0 2-1 3s-3 0-3 2 2 1 2 3 1 2 2 2-1-2 1-3 1-2 0-3-2 0-2-1 2-1 3-2-1-1-2-1z"/></svg>
        www.mvr-elektro.com
      </li>
    </ul>

    <section class="letter-body">
      <p class="salutation">Dear customer,</p>
      <p class="para">Lorem ipsum dolor sit amet, consectetur adipisicing elit, sed do eiusmod tempor incididunt ut labore et dolore magna aliqua. Ut enim ad minim veniam, quis nostrud exercitation ullamco laboris nisi ut aliquip ex ea commodo consequat. Duis aute irure dolor in reprehenderit in voluptate velit esse cillum dolore eu fugiat nulla pariatur. Excepteur sint occaecat cupidatat non proident, sunt in culpa qui officia deserunt mollit anim id est laborum.</p>
      <p class="para">Lorem ipsum dolor sit amet, consectetur adipisicing elit, sed do eiusmod tempor incididunt ut labore et dolore magna aliqua. Ut enim ad minim veniam, quis nostrud exercitation ullamco laboris nisi ut aliquip ex ea commodo consequat. Duis aute irure dolor in reprehenderit in voluptate velit esse cillum dolore eu fugiat nulla pariatur. Excepteur sint occaecat cupidatat non proident, sunt in culpa qui officia deserunt mollit anim id est laborum.</p>
      <p class="para">Lorem ipsum dolor sit amet, consectetur adipisicing elit, sed do eiusmod tempor incididunt ut labore et dolore magna aliqua. Ut enim ad minim veniam, quis nostrud exercitation ullamco laboris nisi ut aliquip ex ea commodo consequat. Duis aute irure dolor in reprehenderit in voluptate velit esse cillum dolore eu fugiat nulla pariatur. Excepteur sint occaecat cupidatat non proident, sunt in culpa qui officia deserunt mollit anim id est laborum.</p>
      <p class="para">Lorem ipsum dolor sit amet, consectetur adipisicing elit, sed do eiusmod tempor incididunt ut labore et dolore magna aliqua. Ut enim ad minim veniam, quis nostrud exercitation ullamco laboris nisi ut aliquip ex ea commodo consequat. Duis aute irure dolor in reprehenderit.</p>
      <p class="closing">Yours Sincerely,</p>
    </section>

    <div class="signature" role="img" aria-label="Handwritten signature of the sender"></div>

    <div class="footer-band"></div>
  </main>
</body>
</html>
```